Baby Boutique Needs a Business Card Design

We need a modern double sided business card design using the attached logo for Little Wren Nook.

Little Wren Nook is a baby boutique which sells only handmade clothing and accessories for both boys and girls. Our store will live exclusively online.

We would like to only use the colors that have been used in the logo.

Target Market(s)

Potential wholesale clients, Small business owners

Industry/Entity Type

Retail

Contact Information for Business Card

Name Gideon R. Falkner (Owner)
Email sales@littlewrennook.example
Main Phone 555-203-7719
Cell phone 555-203-7746
Website www.LittleWrenNook.example

Font styles to use
Sans Serif

Colors

Designer to choose colors to be used in the design.

Requirements
Must have
• -Would like to have icons that indentify the contact information.
• -Include our website
• -Include our tagline in a small area near the bottom. "Handmade Baby Creations"
• -Would like to include Facebook and Instagram Icons
• -
Nice to have
• Would like to have a simple back side with the logo.
• Something along the lines of the meadowfield lending card attached.

```html
<!DOCTYPE html>
<html lang="en">
<head>
<meta charset="utf-8">
<title>Little Wren Nook — Business Card</title>
<link href="https://fonts.googleapis.com/css2?family=Work+Sans:wght@400;500&display=swap" rel="stylesheet">
<style>
  :root {
    --backdrop: #1c1c1d;
    --card: #161616;
    --card-edge: #222223;
    --foil: #e4e4e4;
    --foil-soft: #a9a9a9;
    --gloss: #2c2c2c;
    --rule: #6a6a6a;
  }
  * { margin: 0; padding: 0; box-sizing: border-box; }
  html, body {
    width: 1200px; height: 900px; overflow: hidden;
    background: var(--backdrop);
    font-family: 'Work Sans', Arial, sans-serif;
  }
  .stage {
    position: relative; width: 1200px; height: 900px;
    display: flex; flex-direction: column; align-items: center;
    justify-content: center; gap: 36px;
  }
  .card {
    position: relative; width: 700px; height: 400px;
    background: linear-gradient(135deg, var(--card) 0%, #1d1d1e 60%, var(--card) 100%);
    border: 1px solid var(--card-edge);
  }
  .card-front { display: flex; align-items: center; justify-content: center; }
  .brand-name {
    font-weight: 500; color: var(--foil); letter-spacing: 0.02em;
    line-height: 1.05; text-align: center;
  }
  .card-front .brand-name { font-size: 44px; }
  .card-back .brand-mark {
    position: absolute; left: 40px; top: 110px; width: 230px;
    display: flex; align-items: center; justify-content: center; height: 140px;
  }
  .card-back .brand-name { font-size: 32px; color: var(--gloss); }
  .divider {
    position: absolute; left: 300px; top: 85px; width: 1px; height: 200px;
    background: var(--rule);
  }
  .contact { position: absolute; left: 335px; top: 92px; color: var(--foil); }
  .person-name { font-size: 26px; font-weight: 500; letter-spacing: 0.04em; }
  .person-role { font-size: 15px; color: var(--foil-soft); letter-spacing: 0.05em; margin-top: 2px; }
  .contact-list { list-style: none; margin-top: 26px; }
  .contact-list li {
    display: flex; align-items: center; gap: 12px;
    font-size: 17px; letter-spacing: 0.05em; line-height: 1.45;
  }
  .contact-list svg { width: 12px; height: 12px; flex: none; }
  .tagline {
    position: absolute; left: 0; right: 0; bottom: 42px; text-align: center;
    font-size: 17px; letter-spacing: 0.06em; color: var(--foil-soft);
  }
</style>
</head>
<body>
<main class="stage">
  <section class="card card-front">
    <p class="brand-name">Little Wren<br>Nook</p>
  </section>

  <section class="card card-back">
    <div class="brand-mark"><p class="brand-name">Little Wren<br>Nook</p></div>
    <div class="divider"></div>
    <div class="contact">
      <p class="person-name">Gideon R. Falkner</p>
      <p class="person-role">Owner</p>
      <ul class="contact-list">
        <li>
          <svg viewBox="0 0 12 12" aria-hidden="true"><path d="M2.5 1 L4.5 1 L5 3.5 L3.8 4.3 Q4.8 6.8 7.7 8.2 L8.5 7 L11 7.5 L11 9.5 Q11 11 9.5 11 Q1 10 1 2.5 Q1 1 2.5 1Z" fill="var(--foil)"/></svg>
          555-203-7719
        </li>
        <li>
          <svg viewBox="0 0 12 12" aria-hidden="true"><rect x="3" y="0.8" width="6" height="10.4" rx="1" fill="none" stroke="var(--foil)" stroke-width="1.2"/><circle cx="6" cy="9.3" r="0.7" fill="var(--foil)"/></svg>
          555-203-7746
        </li>
        <li>
          <svg viewBox="0 0 12 12" aria-hidden="true"><rect x="1" y="2.5" width="10" height="7" fill="none" stroke="var(--foil)" stroke-width="1.2"/><path d="M1 2.8 L6 6.5 L11 2.8" fill="none" stroke="var(--foil)" stroke-width="1.2"/></svg>
          sales@littlewrennook.example
        </li>
        <li>
          <svg viewBox="0 0 12 12" aria-hidden="true"><circle cx="6" cy="6" r="5" fill="none" stroke="var(--foil)" stroke-width="1.1"/><ellipse cx="6" cy="6" rx="2.2" ry="5" fill="none" stroke="var(--foil)" stroke-width="1"/><path d="M1 6 H11" stroke="var(--foil)" stroke-width="1"/></svg>
          www.LittleWrenNook.example
        </li>
      </ul>
    </div>
    <p class="tagline">Handmade Baby Creations</p>
  </section>
</main>
</body>
</html>
```